Keystonery Billboard - Financial Services Company (Investments, Tax Planning and Insurance)

Our new office has a billboard directly above the office building. We'd like something eye-catching with a strong Call to Action, with the main part of the billboard being under 7 words if possible. We'd like you to include a way to get ahold of us (either our website keystoneryllc.example or our phone number 302-418-2907. You may also include in small font something to indicate that we've been serving the area since 1980 (the DE area, the tri-state area, the Marlowe Hollow, etc.)

We offer financial planning, tax planning, and insurance, and we help our clients to focus on their goals and happiness by providing everything they need for lifelong wealth under one roof.

Our logos are attached, we use a triangle logo with green and gray. We use the tagline "discover lasting prosperity" but this does not need to be included.

Potential ideas we have seen from other financial companies-
- the concept that the driver spends more time looking at billboards than planning for their retirement
-something along the lines of "everything you need for your finances is in this building right here" planning, investments, taxes, insurance"
-don't spend your time worrying about retirement, let us help you plan for it
-are you working for your money, or is it working for you?
- retirement takes planning, we're here to help
- ready to retire? talk to us
- need investment advice?
- need help investing?
- crossing your fingers isn't a retirement plan. we can help.
- retiring soon? you need help.

Those are just general ideas, please feel free to be creative.

brand colors:
#00b585
#00b185
#000000
#ffffff
#6d6f75
#6d6f75
#6f7074
#021712
#052e24

```html
<!DOCTYPE html>
<html lang="en">
<head>
<meta charset="UTF-8">
<title>Keystonery Billboard</title>
<link href="https://fonts.googleapis.com/css2?family=Montserrat:wght@600;800&family=Noto+Serif:wght@700&display=swap" rel="stylesheet">
<style>
  :root {
    --green-deep: #02402a;
    --green-mid: #1f8a58;
    --green-light: #66f0a0;
    --brand-green: #00a86b;
    --bar-green: #053d2a;
    --gray-text: #6d6f75;
    --panel-white: #f4f4f4;
    --panel-gray: #e6e6e6;
    --white: #ffffff;
    --gold: #f2c230;
    --gold-dark: #c8961a;
    --floor: #6e5f66;
  }
  * { box-sizing: border-box; margin: 0; padding: 0; }
  html, body { width: 1000px; height: 1200px; overflow: hidden; }
  body {
    background: linear-gradient(180deg, #e4e4e4, #c9c9c9);
    font-family: "Montserrat", sans-serif;
    position: relative;
  }
  .billboard {
    position: absolute;
    left: 20px; top: 360px;
    width: 960px; height: 480px;
    background: var(--white);
    box-shadow: 0 18px 30px rgba(0,0,0,0.35);
    overflow: hidden;
  }
  .hero {
    position: absolute; left: 0; top: 10px;
    width: 960px; height: 322px;
    background: linear-gradient(90deg, var(--green-deep) 0%, var(--green-mid) 45%, #4cd48a 75%, var(--green-light) 100%);
  }
  .floor {
    position: absolute; left: 0; bottom: 0;
    width: 100%; height: 48px;
    background: linear-gradient(180deg, #4f4a4e, var(--floor) 60%, #5d5157);
    opacity: 0.85;
  }
  .brand-tab {
    position: absolute; right: 0; top: 0;
    width: 300px; height: 66px;
    background: var(--white);
    clip-path: polygon(0 0, 100% 0, 100% 100%, 14% 100%);
  }
  .brand-name {
    position: absolute; right: 30px; top: 6px;
    font-family: "Noto Serif", serif; font-weight: 700;
    font-size: 32px; color: var(--brand-green);
    display: flex; align-items: center; gap: 8px;
  }
  .brand-mark { width: 14px; height: 14px; background: var(--brand-green); }
  .brand-tagline {
    position: absolute; right: 30px; top: 48px;
    font-size: 7px; letter-spacing: 2.2px; color: var(--gray-text);
    text-transform: uppercase;
  }
  .headline {
    position: absolute; left: 44px; top: 36px;
    color: var(--white); font-weight: 800; line-height: 0.98;
    white-space: nowrap;
  }
  .headline .big { display: block; font-size: 82px; letter-spacing: 1px; }
  .headline .sub { display: block; margin-top: 10px; font-size: 56px; }
  .headline .sub small { font-size: 36px; font-weight: 800; }
  .coin-art {
    position: absolute; left: 718px; top: 82px;
    width: 160px; height: 240px;
    border-radius: 40px;
    background: radial-gradient(circle at 40% 35%, #ffe070, var(--gold) 55%, var(--gold-dark));
  }
  .services {
    position: absolute; left: 0; top: 332px;
    width: 960px; height: 76px; display: flex;
  }
  .service {
    display: flex; align-items: center; gap: 14px;
    flex: none; white-space: nowrap; overflow: hidden;
    font-family: "Noto Serif", serif; font-weight: 700;
    font-size: 22px; color: var(--gray-text);
    background: var(--panel-white);
  }
  .service:nth-child(1) { width: 252px; padding-left: 44px; }
  .service:nth-child(2) { width: 253px; padding-left: 18px; background: var(--panel-gray); }
  .service:nth-child(3) { width: 172px; padding-left: 14px; }
  .service:nth-child(4) { width: 283px; padding-left: 28px; background: var(--panel-gray); }
  .service svg { width: 54px; height: 54px; flex: none; }
  .contact {
    position: absolute; left: 0; top: 408px;
    width: 960px; height: 72px;
    background: var(--bar-green);
    color: var(--white); font-weight: 800; font-size: 34px;
    display: flex; align-items: center; padding-left: 42px; gap: 12px;
    white-space: nowrap;
  }
  .contact svg { width: 40px; height: 40px; flex: none; }
  .contact .divider { width: 3px; height: 40px; background: var(--white); margin: 0 6px; }
</style>
</head>
<body>
  <div class="billboard">
    <div class="hero">
      <div class="floor"></div>
      <div class="brand-tab">
        <div class="brand-name"><span class="brand-mark"></span>Keystonery</div>
        <div class="brand-tagline">Discover lasting prosperity</div>
      </div>
      <h1 class="headline">
        <span class="big">WORRYING</span>
        <span class="big">ABOUT</span>
        <span class="sub"><small>YOUR MONEY?</small> US TOO!</span>
      </h1>
      <div class="coin-art" role="img" aria-label="Large golden 3D dollar sign standing on a surface"></div>
    </div>

    <div class="services">
      <div class="service">
        <svg viewBox="0 0 54 54"><circle cx="27" cy="27" r="27" fill="#0f9a5c"/><circle cx="27" cy="27" r="14" fill="none" stroke="#fff" stroke-width="2" stroke-dasharray="4 2"/><circle cx="27" cy="27" r="8" fill="none" stroke="#fff" stroke-width="2"/><text x="27" y="32" font-size="12" font-weight="700" text-anchor="middle" fill="#fff" font-family="Montserrat, sans-serif">$</text></svg>
        Planning
      </div>
      <div class="service">
        <svg viewBox="0 0 54 54"><circle cx="27" cy="27" r="27" fill="#0f9a5c"/><circle cx="27" cy="19" r="8" fill="none" stroke="#fff" stroke-width="2"/><text x="27" y="23" font-size="10" font-weight="700" text-anchor="middle" fill="#fff" font-family="Montserrat, sans-serif">$</text><path d="M27 27v12M27 33c-4 0-7-3-8-6M27 33c4 0 7-3 8-6M18 40h18" stroke="#fff" stroke-width="2" fill="none"/></svg>
        Investments
      </div>
      <div class="service">
        <svg viewBox="0 0 54 54"><circle cx="27" cy="27" r="27" fill="#0f9a5c"/><rect x="16" y="14" width="18" height="26" rx="2" fill="none" stroke="#fff" stroke-width="2"/><text x="18" y="22" font-size="6" font-weight="700" fill="#fff" font-family="Montserrat, sans-serif">TAX</text><path d="M19 27h12M19 31h12M19 35h8" stroke="#fff" stroke-width="1.6"/><rect x="30" y="26" width="10" height="14" fill="#0f9a5c" stroke="#fff" stroke-width="1.6"/></svg>
        Taxes
      </div>
      <div class="service">
        <svg viewBox="0 0 54 54"><circle cx="27" cy="27" r="27" fill="#0f9a5c"/><path d="M16 24a12 10 0 0 1 24 0z" fill="none" stroke="#fff" stroke-width="2"/><path d="M28 24v6" stroke="#fff" stroke-width="2"/><path d="M12 36l6-4h8l4 2h8M12 36l6 4h12l10-6" stroke="#fff" stroke-width="2" fill="none"/></svg>
        Insurance
      </div>
    </div>

    <div class="contact">
      <svg viewBox="0 0 40 40"><circle cx="20" cy="20" r="19" fill="#fff"/><path d="M13 11l5 1 2 5-3 2c1 3 3 5 6 6l2-3 5 2 1 5c-1 2-3 3-5 2-8-2-14-8-16-16-1-2 1-4 3-4z" fill="#053d2a"/></svg>
      <span class="phone">302-418-2907</span>
      <span class="divider"></span>
      <svg viewBox="0 0 40 40"><circle cx="20" cy="20" r="19" fill="#fff"/><circle cx="20" cy="20" r="11" fill="none" stroke="#053d2a" stroke-width="2"/><ellipse cx="20" cy="20" rx="5" ry="11" fill="none" stroke="#053d2a" stroke-width="2"/><path d="M9 20h22M11 14h18M11 26h18" stroke="#053d2a" stroke-width="1.6"/></svg>
      <span class="web">keystoneryllc.example</span>
    </div>
  </div>
</body>
</html>
```